Banner ads for LP that work with same theme as below banners

Love the banner ads below. Need more with attached photos. But use the same wording, font as in below banner ads. Should be LP size 1200/627 so I can use for Pixorly and LP. Looking for great ads to use as LP ads. We do lots of ads so it will be worth your time to enter this contest you will be rewarded with a ton of work. Need several banner ads that work together. So maybe 1 of the dresses, 1 of the sweater, 1 of the leggings, 1 of the jacket

Target Market(s)

Women 24-45

Industry/Entity Type

Fashion

Requirements
Must have
• Banner ads that work for LP and Pixorly
Nice to have
• Several options to choose from
Should not have
• not sure

```html
<!DOCTYPE html>
<html lang="en">
<head>
<meta charset="utf-8">
<title>Our Best Sweater Ever – Banner</title>
<link rel="stylesheet" href="https://fonts.googleapis.com/css2?family=Playball&family=Playfair+Display:wght@700;900&family=Lato:wght@400&display=swap">
<style>
  :root {
    --wall-light: #f5f3f2;
    --wall-mid: #ecebe9;
    --wall-shadow: #e0dfde;
    --knit-light: #d4d1e0;
    --knit-mid: #c4c0d4;
    --script-grey: #c2c1c1;
    --headline-grey: #4a4948;
    --button-fill: #c8c7c6;
    --button-ink: #3a2a0e;
  }
  * { margin: 0; padding: 0; box-sizing: border-box; }
  html, body { width: 1200px; height: 627px; overflow: hidden; }
  .banner {
    position: relative;
    width: 1200px;
    height: 627px;
    overflow: hidden;
    background: radial-gradient(ellipse 900px 600px at 62% 30%, var(--wall-light) 0%, var(--wall-mid) 65%, var(--wall-shadow) 100%);
  }
  .model-photo {
    position: absolute;
    left: 135px;
    top: 0;
    width: 290px;
    height: 627px;
    background: linear-gradient(180deg, var(--wall-mid) 0%, var(--knit-light) 30%, var(--knit-mid) 100%);
  }
  .script-line {
    position: absolute;
    left: 614px;
    width: 400px;
    text-align: center;
    font-family: "Playball", cursive;
    font-size: 64px;
    line-height: 1;
    color: var(--script-grey);
  }
  .script-line--top { top: 180px; }
  .script-line--bottom { top: 326px; left: 610px; }
  .product-name {
    position: absolute;
    left: 565px;
    top: 245px;
    width: 500px;
    text-align: center;
    font-family: "Playfair Display", serif;
    font-weight: 900;
    font-size: 78px;
    line-height: 1;
    letter-spacing: 8px;
    padding-left: 8px;
    color: var(--headline-grey);
  }
  .shop-button {
    position: absolute;
    left: 663px;
    top: 406px;
    width: 305px;
    height: 49px;
    background: var(--button-fill);
    display: flex;
    align-items: center;
    justify-content: center;
    font-size: 24px;
    letter-spacing: 2px;
    color: var(--button-ink);
    text-decoration: none;
  }
  .shop-button strong { font-family: "Playfair Display", serif; font-weight: 700; }
  .shop-button .light { font-family: "Lato", sans-serif; font-weight: 400; margin: 0 10px; }
</style>
</head>
<body>
  <main class="banner">
    <div class="model-photo" role="img" aria-label="Model wearing an oversized lilac knit turtleneck sweater with black leggings against a white wall"></div>
    <p class="script-line script-line--top">Our Best</p>
    <h1 class="product-name">SWEATER</h1>
    <p class="script-line script-line--bottom">Ever!</p>
    <a class="shop-button" href="#"><strong>SHOP</strong><span class="light">THE</span><strong>LOOK</strong></a>
  </main>
</body>
</html>
```